Business card for my new company (Accounting firm)

I need a business card for my new business Brightwell Advisory and Ledger SA. Our services are accounting, tax, audit and financial management. Our customers are small companies, start-ups and new companies. The final design has to show financial security, trust and growth. Please find our logo attached to the business card. Text for the business card: Brightwell Advisory and Ledger SA Tomas Varenholt Director and Founder Certified Accountant Tel. 022 418 57 34 tv@clairevalconseil.ch www.clairevalconseil.ch Rue des Vergières 27 1201 Geneva
Target Market(s)
Our customers are small companies, start-ups and new companies.
Industry/Entity Type
Finance And Accounting
Contact Information for Business Card
Claireval Conseil et Comptes SA
Tomas Varenholt
Directeur et Fondateur
Expert-comptable diplômé
Tél. 022 418 57 34
tv@clairevalconseil.ch
www.clairevalconseil.ch
Rue des Vergières 27
1201 Genève

```html
<!DOCTYPE html>
<html lang="en">
<head>
<meta charset="utf-8">
<title>Claireval Conseil et Comptes SA – Business Card</title>
<link rel="stylesheet" href="https://fonts.googleapis.com/css2?family=Lato:wght@400;700&display=swap">
<style>
  :root {
    --page-bg: #d9d9d9;
    --card-dark: #3d3d3f;
    --blue-light: #2eaee2;
    --blue-mid: #1f8dd0;
    --blue-deep: #16679a;
    --white: #ffffff;
    --muted: #d6d6d6;
  }
  * { box-sizing: border-box; margin: 0; padding: 0; }
  html, body {
    width: 1200px; height: 802px; overflow: hidden;
    background: var(--page-bg);
    font-family: "Lato", sans-serif;
  }
  .canvas { position: relative; width: 1200px; height: 802px; }
  .card {
    position: absolute; top: 274px; width: 443px; height: 265px;
    box-shadow: 0 2px 6px rgba(0,0,0,0.25);
    overflow: hidden;
  }
  .card--front {
    left: 136px; color: var(--white);
    background: linear-gradient(180deg, var(--blue-mid) 0%, var(--blue-light) 45%, var(--blue-light) 62%, var(--blue-deep) 100%);
  }
  .card--back { left: 624px; background: var(--card-dark); }

  .holder { position: absolute; left: 23px; top: 35px; }
  .holder__name { font-weight: 700; font-size: 15px; letter-spacing: -0.2px; line-height: 17px; }
  .holder__role { font-size: 12.5px; line-height: 15px; }

  .contact { position: absolute; left: 23px; top: 107px; list-style: none; }
  .contact__item { display: flex; align-items: center; gap: 9px; font-size: 12.5px; line-height: 16px; }
  .contact__icon { width: 12px; height: 12px; fill: var(--white); }

  .address { position: absolute; left: 23px; top: 169px; font-style: normal; font-size: 12.5px; line-height: 16px; }

  .brand {
    position: absolute; left: 0; right: 0; top: 70px;
    display: flex; flex-direction: column; align-items: center; gap: 16px;
  }
  .brand__dot { width: 56px; height: 56px; border-radius: 50%; background: var(--blue-light); }
  .brand__name {
    font-weight: 400; font-size: 24px; letter-spacing: 2px;
    color: var(--white); text-transform: uppercase;
  }
</style>
</head>
<body>
<main class="canvas">
  <section class="card card--front" aria-label="Card front">
    <div class="holder">
      <p class="holder__name">SA TOMAS VARENHOLT</p>
      <p class="holder__role">Director and Founder</p>
      <p class="holder__role">Certified Accountant</p>
    </div>
    <ul class="contact">
      <li class="contact__item">
        <svg class="contact__icon" viewBox="0 0 12 12" aria-hidden="true"><path d="M1 4c0-2 2-3 5-3s5 1 5 3v1H8.5V3.8h-5V5H1z"/><path d="M3 6h6l1.5 4.5h-9z"/></svg>
        <span>022 418 57 34</span>
      </li>
      <li class="contact__item">
        <svg class="contact__icon" viewBox="0 0 12 12" aria-hidden="true"><path d="M1 2.5h10v7H1z" /><path d="M1.5 3l4.5 3.5L10.5 3" stroke="#2eaee2" stroke-width="1.2" fill="none"/></svg>
        <span>tv@clairevalconseil.ch</span>
      </li>
      <li class="contact__item">
        <svg class="contact__icon" viewBox="0 0 12 12" aria-hidden="true"><circle cx="6" cy="6" r="5"/><path d="M3 4c1 0 2 1 1.5 2S5 8 6 8.5M7 2.5c0 1 1 1.5 2 1.5" stroke="#2eaee2" stroke-width="1" fill="none"/></svg>
        <span>www.clairevalconseil.ch</span>
      </li>
    </ul>
    <address class="address">
      Rue des Vergières 27<br>
      1201 Geneva
    </address>
  </section>

  <section class="card card--back" aria-label="Card back">
    <div class="brand">
      <span class="brand__dot" aria-hidden="true"></span>
      <p class="brand__name">Claireval Conseil</p>
    </div>
  </section>
</main>
</body>
</html>
```